Logo and Card design for KRV Home Solutions LLC

I need an edgier logo and business card designs. Current logo attached. I like the colors below. I would like the logo to incorporate a home in the design.
Title = Principal-Acquisitions
Email:KRVHOMESOLUTIONS@fernmail.example
555-214-0937
facebook
IG
2 sided business card with the front being contact info a slogan about selling a home fast. The back incorporating What we do. Buy houses, land, or commercial property as is. We find solutions to make the process of selling simple and fair.

Target Market(s)

Motivated house sellers.

Industry/Entity Type

Business

Contact Information for Business Card

Who we are: We are a Faith based Real Estate Investment Company. We pay cash for homes in any condition and can close quick. Whatever the reason you need to sell fast, we can help. We believe in creating win-win solutions to help you in your time of need. We care! We can help!

Logo Text

KRV Home Solutions LLC

Font styles to use
Sans Serif

Colors
33a6d7
0355a3
85abd2
cee9f5
9d9d9d
b2b2b2
ffffff

Requirements
Must have
• Old logo attached. I want something edgier.
• Company name, phone number, description on the back of what we can do. Pay all cash. Buy in as is condition. No fees,Commisions or closing costs.Close quick. No hassles with solutions to meet your unique situation.
• Call today for an offer within 24 hours.

```html
<!DOCTYPE html>
<html lang="en">
<head>
<meta charset="utf-8">
<title>KRV Home Solutions – Business Card</title>
<link href="https://fonts.googleapis.com/css2?family=Oswald:wght@600&family=Work+Sans:wght@400;500;600&display=swap" rel="stylesheet">
<style>
  :root {
    --navy: #1f3469;
    --navy-light: #2c4278;
    --white: #ffffff;
    --ink: #3a3a3a;
    --grey: #6d6d6d;
    --accent: #f2b552;
    --backdrop: #1c1c1e;
  }
  * { box-sizing: border-box; margin: 0; padding: 0; }
  html, body { width: 1200px; height: 963px; overflow: hidden; }
  body {
    background: var(--backdrop);
    font-family: "Work Sans", sans-serif;
    display: flex;
    flex-direction: column;
    align-items: center;
    justify-content: center;
    gap: 50px;
  }
  .card {
    width: 700px;
    height: 400px;
    position: relative;
    overflow: hidden;
    box-shadow: 0 12px 30px rgba(0,0,0,.5);
  }

  /* Front */
  .card-front { background: var(--white); }
  .identity {
    position: absolute;
    left: 40px;
    top: 150px;
    width: 270px;
  }
  .company-name {
    font-family: "Oswald", sans-serif;
    font-weight: 600;
    font-size: 30px;
    line-height: 1;
    color: var(--navy);
    text-transform: uppercase;
    letter-spacing: -0.5px;
    white-space: nowrap;
  }
  .job-title {
    margin-top: 6px;
    font-size: 15px;
    color: var(--grey);
    white-space: nowrap;
  }
  .divider {
    position: absolute;
    left: 318px;
    top: 140px;
    width: 2px;
    height: 96px;
    background: var(--accent);
  }
  .contact-list {
    position: absolute;
    left: 336px;
    top: 138px;
    list-style: none;
    font-size: 15px;
    color: var(--ink);
  }
  .contact-list li {
    display: flex;
    align-items: center;
    gap: 9px;
    height: 25px;
    white-space: nowrap;
  }
  .contact-list svg { width: 15px; height: 15px; flex: none; }
  .slogan {
    position: absolute;
    left: 40px;
    bottom: 80px;
    font-size: 16px;
    font-weight: 500;
    letter-spacing: 4px;
    color: var(--ink);
    text-transform: uppercase;
  }

  /* Back */
  .card-back {
    background: linear-gradient(160deg, var(--navy) 0%, var(--navy-light) 100%);
    color: var(--white);
  }
  .brand-mark {
    position: absolute;
    left: 0; right: 0;
    top: 80px;
    text-align: center;
    font-weight: 600;
    font-size: 34px;
    letter-spacing: 2px;
    text-transform: uppercase;
  }
  .offer {
    position: absolute;
    left: 50px; right: 50px;
    top: 195px;
    text-align: center;
    font-size: 17px;
    line-height: 1.55;
    letter-spacing: 0.5px;
  }
</style>
</head>
<body>

  <section class="card card-front" aria-label="Business card front">
    <div class="identity">
      <h1 class="company-name">KRV Home Solutions</h1>
      <p class="job-title">Principal-Acquisitions</p>
    </div>
    <div class="divider"></div>
    <ul class="contact-list">
      <li>
        <svg viewBox="0 0 16 16" aria-hidden="true"><rect width="16" height="16" rx="4" fill="var(--navy)"/><path d="M5 4.2c.5-.4 1-.3 1.3.2l.7 1.3c.2.4.1.8-.2 1.1l-.5.4c.4.9 1.1 1.6 2 2l.4-.5c.3-.3.7-.4 1.1-.2l1.3.7c.5.3.6.8.2 1.3l-.5.6c-.5.5-1.3.6-2 .3C7 10.6 5.4 9 4.6 7c-.3-.7-.2-1.5.3-2z" fill="var(--white)"/></svg>
        555-214-0937
      </li>
      <li>
        <svg viewBox="0 0 16 16" aria-hidden="true"><circle cx="8" cy="8" r="7" fill="var(--navy)"/></svg>
        /krvhomesolutions
      </li>
      <li>
        <svg viewBox="0 0 16 16" aria-hidden="true"><circle cx="8" cy="8" r="7" fill="var(--navy)"/></svg>
        @krvhomesolutions
      </li>
      <li>
        <svg viewBox="0 0 16 16" aria-hidden="true"><rect width="16" height="16" rx="4" fill="var(--navy)"/><rect x="3.5" y="5" width="9" height="6.5" rx="1" fill="none" stroke="var(--white)" stroke-width="1.2"/><path d="M3.8 5.4 8 8.6l4.2-3.2" fill="none" stroke="var(--white)" stroke-width="1.2"/></svg>
        KRVHOMESOLUTIONS@fernmail.example
      </li>
    </ul>
    <p class="slogan">Selling a home fast</p>
  </section>

  <section class="card card-back" aria-label="Business card back">
    <div class="brand-mark">KRV Home Solutions</div>
    <p class="offer">
      Pay all cash. Buy in as is condition. No fees,Commisions<br>
      or closing costs.Close quick. No hassles with solutions<br>
      to meet your unique situation.<br>
      Call today for an offer within 24 hours.
    </p>
  </section>

</body>
</html>
```